Equine Podcast Cover Art Design

We need catchy cover art for a horse related podcast "Ride Onward Together"
Brief show description"
Whether you want to ride to experience horses, develop yourself to the next level as a horseman/horsewoman or ride to improve your physical and mental health, we are committed to helping you Ride Onward TogetherĀ®. Join us as we explore the nuance of equine management and sports as well as interview industry professionals to provide you with the knowledge necessary to be a better partner for your equine friends.
I have uploaded two existing logos we use for various purposes to give you an idea of existing style.
Target Market(s)
Horse owners and other equine professionals
Look and feel
Each slider illustrates characteristics of the customer's brand and the style your logo design should communicate.

```html
<!DOCTYPE html>
<html lang="en">
<head>
<meta charset="utf-8">
<title>Ride Onward Together® Podcast Cover</title>
<link rel="stylesheet" href="https://fonts.googleapis.com/css2?family=Abril+Fatface&family=Bebas+Neue&family=Poppins:wght@400;600&display=swap">
<style>
  :root {
    --title-red: #b82236;
    --ink-white: #ffffff;
    --bg-forest-dark: #2a2430;
    --bg-forest-mid: #3b3f2c;
    --bg-field: #4a5138;
    --horse-brown: #8a4d22;
    --horse-dark: #3a2214;
    --rider-navy: #1d1f2a;
  }
  * { margin: 0; padding: 0; box-sizing: border-box; }
  html, body { width: 1200px; height: 1200px; overflow: hidden; }
  body { background: var(--bg-forest-dark); }
  .cover {
    position: relative;
    width: 1200px;
    height: 1200px;
    overflow: hidden;
  }
  .farm-aerial {
    position: absolute;
    inset: 0;
    background:
      radial-gradient(ellipse 45% 40% at 40% 50%, var(--bg-field) 0%, transparent 70%),
      radial-gradient(ellipse 70% 60% at 50% 55%, var(--bg-forest-mid) 0%, transparent 80%),
      linear-gradient(180deg, #2b2533 0%, #30302b 50%, #2c2530 100%);
  }
  .rider-photo {
    position: absolute;
    left: 640px;
    top: 123px;
    width: 555px;
    height: 930px;
    border-radius: 40% 30% 20% 35% / 20% 25% 30% 40%;
    background:
      radial-gradient(ellipse 35% 20% at 50% 18%, var(--rider-navy) 0%, transparent 80%),
      radial-gradient(ellipse 60% 55% at 50% 55%, var(--horse-brown) 0%, var(--horse-dark) 75%, transparent 100%);
  }
  .show-title { font-weight: normal; }
  .title-top {
    position: absolute;
    left: 98px;
    top: 40px;
    font-family: "Abril Fatface", serif;
    color: var(--title-red);
    font-size: 200px;
    line-height: 0.95;
    letter-spacing: -4px;
    transform: scaleX(0.78);
    transform-origin: left top;
  }
  .title-main {
    position: absolute;
    left: 98px;
    top: 543px;
    font-family: "Bebas Neue", sans-serif;
    color: var(--ink-white);
    font-size: 300px;
    line-height: 1;
    letter-spacing: 2px;
    white-space: nowrap;
    transform: scaleY(1.5);
    transform-origin: left top;
  }
  .title-reg {
    position: absolute;
    left: 1052px;
    top: 560px;
    font-family: "Poppins", sans-serif;
    font-size: 44px;
    font-weight: 600;
    color: var(--ink-white);
    line-height: 1;
  }
  .farm-mark {
    position: absolute;
    left: 98px;
    top: 1040px;
    display: flex;
    align-items: center;
    gap: 12px;
    color: var(--ink-white);
    font-family: "Poppins", sans-serif;
    font-weight: 600;
    font-size: 20px;
    letter-spacing: 1px;
    text-transform: uppercase;
  }
  .farm-mark .dot {
    width: 22px;
    height: 22px;
    border: 2px solid var(--ink-white);
    border-radius: 50%;
  }
  .format-label {
    position: absolute;
    left: 916px;
    top: 1070px;
    font-family: "Poppins", sans-serif;
    color: var(--ink-white);
    font-size: 34px;
    letter-spacing: 0.22em;
  }
</style>
</head>
<body>
  <main class="cover">
    <div class="farm-aerial" role="img" aria-label="Aerial view of a horse farm with barns, arena and paddocks surrounded by autumn forest"></div>
    <div class="rider-photo" role="img" aria-label="Rider in helmet and navy jacket on a bay horse jumping"></div>
    <h1 class="show-title">
      <span class="title-top">Ride<br>Onward</span>
      <span class="title-main">TOGETHER</span>
      <span class="title-reg">®</span>
    </h1>
    <div class="farm-mark"><span class="dot"></span>Stillwater Acres</div>
    <p class="format-label">podcast</p>
  </main>
</body>
</html>
```